Christian Media Company Website

I am looking to design an easy to follow, sleek, creative website for my Christian video Bible study platform. On this platform you will be able to sign up to have access to dozens of free high-quality video Bible studies. With that being said There will be a total of 3 pages needed.

First, I will need the home page. This should contain all critical information to inform the customer. The design should be easy to follow, professional, and creative. I will post to some websites I like, if you just copy the website in your design will be removed immediately.

Secondly, we will need a landing Bible study page for people to look through the Bible studies to select one. I have uploaded Study images below with the aspect ratio I want for the design (for each Bible study image). There should be 2 sections Topical studies and Doctrinal Studies (with series under each section). I would like for people to be able to slide left or right through the studies under each category.

Lastly, we will need a video series page. This page needs to have the video they are watching, a playlist of the other videos, as well as a place to put the speaker's image and description. We will have studies that they can download so please make a place for this.

I will upload our color in the files along with our logo! Looking forward to seeing what you all will come up with!

Websites I like :
https://lanternvale.org/
https://www.quillharborfilms.org/
https://www.dunmorel.com/
https://tessavint.org/

Target Market(s)

Christians

Industry/Entity Type

Christian Video Design

Coding

Coded - Design and coding required

Number of Pages Required

3 page

Font styles to use
Sans Serif

Colors
00AB8E
00BBA5
67D7C9
C6EFE9
E9F9F6

Requirements
Should not have
• Pre-Used Templates

```html
<!DOCTYPE html>
<html lang="en">
<head>
<meta charset="utf-8">
<title>Hearthway Studies – Christian Bible Study</title>
<link href="https://fonts.googleapis.com/css2?family=Poppins:wght@400;500;600;700;800&family=Lato:wght@400;700&display=swap" rel="stylesheet">
<style>
:root{
  --teal:#00AB8E;
  --teal-2:#00BBA5;
  --teal-3:#67D7C9;
  --teal-4:#C6EFE9;
  --teal-5:#E9F9F6;
  --ink:#262626;
  --muted:#8a8a8a;
  --about-bg:#eeeef4;
  --field:#f5f5f8;
  --footer:#222222;
  --white:#ffffff;
}
*{box-sizing:border-box;margin:0;padding:0}
html,body{width:1200px;height:3768px;overflow:hidden}
body{position:relative;font-family:"Lato",sans-serif;color:var(--ink);background:var(--white)}
.abs{position:absolute}
.heading{font-family:"Poppins",sans-serif}
.btn{position:absolute;display:flex;align-items:center;justify-content:center;font-family:"Poppins",sans-serif;font-weight:600;font-size:15px;text-transform:uppercase}
.btn-solid{background:var(--teal);color:var(--white)}
.btn-line{border:2px solid var(--teal);color:var(--teal);background:var(--white)}

/* top bar */
.topbar{position:absolute;left:0;top:0;width:1200px;height:51px;background:var(--teal-2)}
.topbar .item{position:absolute;top:0;height:51px;display:flex;align-items:center;gap:8px;color:var(--white);font-family:"Poppins",sans-serif;font-size:14px;font-weight:500}
.social-dot{position:absolute;width:38px;height:38px;border-radius:50%;background:var(--white);top:7px}

/* nav */
.nav{position:absolute;left:0;top:51px;width:1200px;height:84px;background:var(--white)}
.brand{position:absolute;display:flex;align-items:center;gap:12px;font-family:"Poppins",sans-serif;font-weight:700;text-transform:uppercase;line-height:1.05}
.brand-square{border:3px solid currentColor}
.nav .brand{left:111px;top:14px;color:var(--teal-2);font-size:23px}
.nav .brand-square{width:48px;height:48px}
.nav-links{position:absolute;top:0;height:84px;display:flex;align-items:center;font-family:"Poppins",sans-serif;font-size:15px;font-weight:500}
.nav-links a{position:absolute;text-decoration:none;color:var(--ink);white-space:nowrap}
.nav-links a.active{color:var(--teal-2)}

/* hero */
.hero{position:absolute;left:0;top:135px;width:1200px;height:556px;background:var(--teal)}
.hero-photo{position:absolute;right:0;top:0;width:666px;height:556px;clip-path:polygon(212px 0,666px 0,666px 556px,0 556px);background:linear-gradient(135deg,#c78c4c 0%,#e8c28a 35%,#a34a36 65%,#5b3a2a 100%)}
.hero .eyebrow{position:absolute;left:111px;top:112px;color:var(--white);font-family:"Poppins",sans-serif;font-size:28px;font-weight:400}
.hero h1{position:absolute;left:111px;top:160px;color:var(--white);font-family:"Poppins",sans-serif;font-size:60px;line-height:73px;font-weight:800}
.hero p{position:absolute;left:111px;top:316px;width:460px;color:var(--white);font-size:15.5px;line-height:23px}
.hero .btn{left:111px;top:386px;width:130px;height:48px;border:2px solid var(--white);color:var(--white);font-size:14px}

/* about */
.about{position:absolute;left:0;top:691px;width:1200px;height:455px;background:var(--about-bg);overflow:hidden}
.frame{position:absolute;border:2px solid var(--teal-2)}
.about h2{position:absolute;left:111px;top:80px;font-family:"Poppins",sans-serif;font-size:28px;font-weight:600}
.about p{position:absolute;left:111px;width:940px;font-size:15.3px;line-height:25.6px;color:#333}
.about .btn{left:111px;top:333px;width:129px;height:50px;font-size:14px}

/* series */
.section-title{position:absolute;left:0;width:1200px;text-align:center;font-family:"Poppins",sans-serif;font-size:29px;font-weight:600}
.card{position:absolute;width:315px;height:294px;background:var(--white);box-shadow:0 2px 12px rgba(0,0,0,.12)}
.card-media{position:absolute;left:0;top:0;width:315px;height:215px;display:flex;align-items:center;justify-content:center}
.card-media span{font-family:"Poppins",sans-serif;font-size:34px;font-weight:600;color:var(--white);text-shadow:0 2px 6px rgba(0,0,0,.35)}
.card-foot{position:absolute;left:0;top:215px;width:315px;height:79px}
.card.active .card-foot{background:var(--teal-3)}
.avatar{position:absolute;left:14px;top:20px;width:48px;height:48px;border-radius:50%;background:linear-gradient(160deg,#d9d9d9,#8d2a3a);border:3px solid #eee}
.speaker{position:absolute;left:76px;top:22px;font-family:"Poppins",sans-serif;font-size:15px;font-weight:500}
.role{position:absolute;left:76px;top:46px;font-size:13px;color:var(--muted)}
.card.active .speaker,.card.active .role{color:var(--white)}
.actions{position:absolute;left:190px;top:30px;display:flex;gap:19px}
.actions svg{width:24px;height:24px;fill:none;stroke:#888;stroke-width:1.6;stroke-linecap:round;stroke-linejoin:round}
.card.active .actions svg{stroke:var(--white)}
.play{position:absolute;left:127px;top:78px;width:60px;height:60px;border-radius:50%;background:var(--white);border:5px solid var(--teal-3);display:flex;align-items:center;justify-content:center}

/* blog */
.blog{position:absolute;left:0;top:2093px;width:1200px;height:635px}
.blog h2{position:absolute;left:0;top:62px;width:1200px;text-align:center;color:var(--white);font-family:"Poppins",sans-serif;font-size:29px;font-weight:600}
.post{position:absolute;top:196px;width:315px;height:243px;background:var(--white);border-radius:4px;padding:28px 30px}
.post h3{font-family:"Poppins",sans-serif;font-size:19.5px;font-weight:400;line-height:28px;color:var(--ink)}
.post .date{margin-top:12px;font-family:"Poppins",sans-serif;font-size:15px;color:var(--teal);font-weight:500}
.post p{margin-top:10px;font-size:14.5px;line-height:28px;color:var(--muted)}
.post .more{margin-top:4px;font-family:"Poppins",sans-serif;font-size:15px;color:var(--teal);font-weight:500;display:flex;align-items:center;gap:6px}

/* contact */
.contact-line{position:absolute;left:111px;display:flex;gap:22px;font-size:15px;line-height:23px;color:#333}
.contact-line svg{flex:none;fill:var(--teal-2)}
.map{position:absolute;left:111px;top:3053px;width:467px;height:263px;background:linear-gradient(135deg,#dedede,#c9c9c9 60%,#e4e4e4)}
.field{position:absolute;left:622px;width:464px;background:var(--field);font-size:15px;color:#888;padding:0 30px;display:flex;align-items:center;justify-content:space-between}
.field svg{fill:var(--teal-2)}

/* footer */
.footer{position:absolute;left:0;top:3402px;width:1200px;height:366px;background:var(--footer);color:var(--white)}
.footer .brand{left:111px;top:100px;color:var(--white);font-size:28px}
.footer .brand-square{width:56px;height:56px}
.ring{position:absolute;top:202px;width:50px;height:50px;border-radius:50%;border:2px solid var(--white)}
.col-title{position:absolute;top:92px;font-family:"Poppins",sans-serif;font-size:17px;font-weight:500;text-transform:uppercase}
.links{position:absolute;top:136px;list-style:none;font-size:15px;line-height:26px}
.links li::before{content:"»";margin-right:10px;font-weight:700}
.news-input{position:absolute;left:825px;top:142px;width:264px;height:52px;background:var(--white);color:#999;font-size:15px;padding-left:22px;display:flex;align-items:center}
.footer .btn{left:825px;top:204px;width:126px;height:51px}
.footer-rule{position:absolute;left:111px;top:281px;width:978px;height:1px;background:#3d3d3d}
.copy{position:absolute;left:0;top:308px;width:1200px;text-align:center;font-size:14.5px}
.sr{position:absolute;width:1px;height:1px;overflow:hidden;clip:rect(0 0 0 0)}
</style>
</head>
<body>

<header class="topbar">
  <div class="item" style="left:556px">
    <svg width="16" height="16" viewBox="0 0 24 24" fill="#fff"><path d="M6.6 10.8a15 15 0 0 0 6.6 6.6l2.2-2.2c.3-.3.7-.4 1-.2 1.1.4 2.3.6 3.6.6.6 0 1 .4 1 1V20c0 .6-.4 1-1 1A17 17 0 0 1 3 4c0-.6.4-1 1-1h3.5c.6 0 1 .4 1 1 0 1.3.2 2.5.6 3.6.1.3 0 .7-.2 1z"/></svg>
    +1(555) 014 2270
  </div>
  <div class="item" style="left:746px">
    <svg width="18" height="14" viewBox="0 0 24 18" fill="#fff"><path d="M0 0h24v2L12 9 0 2z M0 4l12 7 12-7v14H0z"/></svg>
    info@hearthway.org
  </div>
  <span class="social-dot" style="left:947px"><span class="sr">Social profile</span></span>
  <span class="social-dot" style="left:997px"><span class="sr">Social profile</span></span>
  <span class="social-dot" style="left:1048px"><span class="sr">Social profile</span></span>
</header>

<nav class="nav">
  <div class="brand"><span class="brand-square"></span><span>Hearthway<br>Studies</span></div>
  <div class="nav-links">
    <a class="active" style="left:473px">HOME</a>
    <a style="left:578px">ABOUT</a>
    <a style="left:691px">OUR VIDEO</a>
    <a style="left:835px">CONTACT</a>
  </div>
  <div class="btn btn-line" style="left:965px;top:18px;width:121px;height:50px;font-size:14px">Sign Up</div>
</nav>

<section class="hero">
  <div class="hero-photo" role="img" aria-label="Young woman praying with folded hands beside a sunlit window, an open Bible on the sill"></div>
  <div class="eyebrow">WELCOME TO</div>
  <h1>CHRISTIAN<br>BIBLE STUDY</h1>
  <p>Lorem ipsum dolor sit amet, consectetur adipiscing elit, sed do eiusmod tempor incididunt ut labore et dolore magna aliqua.</p>
  <div class="btn">Get Started</div>
</section>

<section class="about">
  <div class="frame" style="left:-4px;top:-4px;width:62px;height:110px"></div>
  <div class="frame" style="left:-4px;top:-4px;width:106px;height:72px"></div>
  <div class="frame" style="left:1030px;top:318px;width:200px;height:200px"></div>
  <div class="frame" style="left:1075px;top:274px;width:200px;height:200px"></div>
  <h2>ABOUT US</h2>
  <p style="top:132px">Lorem ipsum dolor sit amet, consectetur adipiscing elit, sed do eiusmod tempor incididunt ut labore et dolore magna aliqua. Ut enim ad minim veniam, quis nostrud exercitation ullamco laboris nisi ut aliquip ex ea commodo consequat. Duis aute irure dolor in reprehenderit in voluptate velit esse cillum dolore eu fugiat nulla pariatur. Excepteur sint occaecat cupidatat non proident, sunt in culpa qui officia deserunt mollit anim id est laborum. Sed ut perspiciatis unde omnis iste natus error sit voluptatem accusantium doloremque</p>
  <p style="top:253px">Nemo enim ipsam voluptatem quia voluptas sit aspernatur aut odit aut fugit, sed quia consequuntur magni dolores eos qui ratione voluptatem sequi nesciunt.</p>
  <div class="btn btn-solid">Learn More</div>
</section>

<h2 class="section-title" style="top:1224px">OUR SERIES</h2>

<svg width="0" height="0" style="position:absolute">
  <defs>
    <symbol id="ic-like" viewBox="0 0 24 24"><path d="M7 11v9H3v-9z M7 11l4-8c1.5 0 2.5 1 2.2 2.6L12.6 9H19c1.2 0 2 1 1.8 2.2l-1.3 7C19.3 19.3 18.5 20 17.5 20H7"/></symbol>
    <symbol id="ic-share" viewBox="0 0 24 24"><path d="M14 5l7 6-7 6v-3.5C8 13.5 5 16 3 19c.5-6 4-10 11-11z"/></symbol>
    <symbol id="ic-down" viewBox="0 0 24 24"><path d="M12 3v12 M7 10l5 5 5-5 M3 16v4h18v-4"/></symbol>
  </defs>
</svg>

<!-- row 1 -->
<article class="card" style="left:111px;top:1307px">
  <div class="card-media" role="img" aria-label="Desert dunes and mountains at sunset with a hot air balloon" style="background:linear-gradient(180deg,#e2a13c 0%,#c9672a 45%,#6b2d14 80%,#2a1a10 100%)"><span>LUKE</span></div>
  <div class="card-foot"><span class="avatar" role="img" aria-label="Speaker portrait"></span><span class="speaker">Aaron Pell</span><span class="role">Lorem ipsum</span>
    <div class="actions"><svg><use href="#ic-like"/></svg><svg><use href="#ic-share"/></svg><svg><use href="#ic-down"/></svg></div></div>
</article>
<article class="card active" style="left:443px;top:1307px">
  <div class="card-media" role="img" aria-label="Anchor resting on a sandy beach beside a wooden boat" style="background:linear-gradient(180deg,#b9c2c4 0%,#a7aaa5 50%,#8e8677 100%);align-items:flex-start;padding-top:20px"><span>ACTS</span></div>
  <div class="play"><svg width="18" height="20" viewBox="0 0 18 20"><path d="M2 1l15 9-15 9z" fill="#00BBA5"/></svg></div>
  <div class="card-foot"><span class="avatar" role="img" aria-label="Speaker portrait"></span><span class="speaker">Aaron Pell</span><span class="role">Lorem ipsum</span>
    <div class="actions"><svg><use href="#ic-like"/></svg><svg><use href="#ic-share"/></svg><svg><use href="#ic-down"/></svg></div></div>
</article>
<article class="card" style="left:774px;top:1307px">
  <div class="card-media" role="img" aria-label="Colourful religious procession in front of an old stone building" style="background:linear-gradient(135deg,#b8a88c 0%,#8e7a5e 45%,#6a4a4a 75%,#b0323a 100%)"><span>JAMES</span></div>
  <div class="card-foot"><span class="avatar" role="img" aria-label="Speaker portrait"></span><span class="speaker">Aaron Pell</span><span class="role">Lorem ipsum</span>
    <div class="actions"><svg><use href="#ic-like"/></svg><svg><use href="#ic-share"/></svg><svg><use href="#ic-down"/></svg></div></div>
</article>

<!-- row 2 -->
<article class="card" style="left:111px;top:1627px">
  <div class="card-media" role="img" aria-label="Man reading a book at a desk under a lamp" style="background:linear-gradient(135deg,#3a3026 0%,#6b5a45 45%,#c2a77e 75%,#4d3f30 100%)"><span>PAUL'S LETTERS</span></div>
  <div class="card-foot"><span class="avatar" role="img" aria-label="Speaker portrait"></span><span class="speaker">Aaron Pell</span><span class="role">Lorem ipsum</span>
    <div class="actions"><svg><use href="#ic-like"/></svg><svg><use href="#ic-share"/></svg><svg><use href="#ic-down"/></svg></div></div>
</article>
<article class="card" style="left:443px;top:1627px">
  <div class="card-media" role="img" aria-label="Bright star over a dark pine forest at night" style="background:radial-gradient(circle at 45% 25%,#ffffff 0,#7fa3c9 8%,#1d3556 40%,#0d1a2a 75%,#0b140d 100%)"><span>CHRISTMAS</span></div>
  <div class="card-foot"><span class="avatar" role="img" aria-label="Speaker portrait"></span><span class="speaker">Aaron Pell</span><span class="role">Lorem ipsum</span>
    <div class="actions"><svg><use href="#ic-like"/></svg><svg><use href="#ic-share"/></svg><svg><use href="#ic-down"/></svg></div></div>
</article>
<article class="card" style="left:774px;top:1627px">
  <div class="card-media" role="img" aria-label="Lone figure standing in a field under a glowing cloudy sky" style="background:linear-gradient(180deg,#8d8a80 0%,#d8b98a 45%,#b98d58 65%,#3e3326 100%)"><span>REVELATION</span></div>
  <div class="card-foot"><span class="avatar" role="img" aria-label="Speaker portrait"></span><span class="speaker">Aaron Pell</span><span class="role">Lorem ipsum</span>
    <div class="actions"><svg><use href="#ic-like"/></svg><svg><use href="#ic-share"/></svg><svg><use href="#ic-down"/></svg></div></div>
</article>

<div class="btn btn-solid" style="left:417px;top:1958px;width:170px;height:48px;font-size:14px">Topical Studies</div>
<div class="btn btn-line" style="left:597px;top:1958px;width:186px;height:48px;font-size:14px">Doctrinal Studies</div>

<section class="blog">
  <svg class="abs" style="left:0;top:0" width="1200" height="635" viewBox="0 0 1200 635">
    <defs><linearGradient id="lens" x1="0" y1="0" x2="0" y2="1"><stop offset="0" stop-color="#43c8b7"/><stop offset="1" stop-color="#20ad99"/></linearGradient></defs>
    <path d="M-100 380 Q600 -380 1300 380 Q600 890 -100 380Z" fill="url(#lens)"/>
  </svg>
  <h2>LATEST BLOG</h2>
  <article class="post" style="left:111px">
    <h3>Sed ut perspiciatis unde omnis iste natus</h3>
    <div class="date">January 20, 2022</div>
    <p>Lorem ipsum dolor sit amet, eiusmod tempor incididunt magna aliqua.</p>
    <div class="more">Learn More <svg width="18" height="10" viewBox="0 0 18 10" fill="none" stroke="#00AB8E" stroke-width="1.6"><path d="M0 5h16 M12 1l4 4-4 4"/></svg></div>
  </article>
  <article class="post" style="left:443px">
    <h3>Sed ut perspiciatis unde omnis iste natus</h3>
    <div class="date">January 20, 2022</div>
    <p>Lorem ipsum dolor sit amet, eiusmod tempor incididunt magna aliqua.</p>
    <div class="more">Learn More <svg width="18" height="10" viewBox="0 0 18 10" fill="none" stroke="#00AB8E" stroke-width="1.6"><path d="M0 5h16 M12 1l4 4-4 4"/></svg></div>
  </article>
  <article class="post" style="left:774px">
    <h3>Sed ut perspiciatis unde omnis iste natus</h3>
    <div class="date">January 20, 2022</div>
    <p>Lorem ipsum dolor sit amet, eiusmod tempor incididunt magna aliqua.</p>
    <div class="more">Learn More <svg width="18" height="10" viewBox="0 0 18 10" fill="none" stroke="#00AB8E" stroke-width="1.6"><path d="M0 5h16 M12 1l4 4-4 4"/></svg></div>
  </article>
</section>

<h2 class="section-title" style="top:2807px">CONTACT US</h2>

<div class="contact-line" style="top:2887px">
  <svg width="20" height="26" viewBox="0 0 20 26"><path d="M10 0a10 10 0 0 0-10 10c0 7 10 16 10 16s10-9 10-16A10 10 0 0 0 10 0zm0 14a4 4 0 1 1 0-8 4 4 0 0 1 0 8z"/></svg>
  <span>Lorem ipsum dolor sit amet, consectetur<br>adipiscing elit, sed do eiusmod tempor</span>
</div>
<div class="contact-line" style="top:2962px">
  <svg width="24" height="18" viewBox="0 0 24 18"><path d="M0 0h24v2L12 9 0 2z M0 4l12 7 12-7v14H0z"/></svg>
  <span>info@hearthway.org</span>
</div>
<div class="map" role="img" aria-label="Map of the United States with a location pin"></div>

<div class="field" style="top:2893px;height:62px">Name <svg width="18" height="18" viewBox="0 0 24 24"><circle cx="12" cy="7" r="5"/><path d="M2 24c0-6 4.5-9 10-9s10 3 10 9z"/></svg></div>
<div class="field" style="top:2971px;height:61px">Email <svg width="20" height="15" viewBox="0 0 24 18"><path d="M0 0h24v2L12 9 0 2z M0 4l12 7 12-7v14H0z"/></svg></div>
<div class="field" style="top:3047px;height:63px">Phone <svg width="18" height="18" viewBox="0 0 24 24"><path d="M6.6 10.8a15 15 0 0 0 6.6 6.6l2.2-2.2c.3-.3.7-.4 1-.2 1.1.4 2.3.6 3.6.6.6 0 1 .4 1 1V20c0 .6-.4 1-1 1A17 17 0 0 1 3 4c0-.6.4-1 1-1h3.5c.6 0 1 .4 1 1 0 1.3.2 2.5.6 3.6.1.3 0 .7-.2 1z"/></svg></div>
<div class="field" style="top:3124px;height:131px;align-items:flex-start;padding-top:22px">Message</div>
<div class="btn btn-solid" style="left:622px;top:3268px;width:111px;height:48px;font-size:14px">Submit</div>

<footer class="footer">
  <div class="brand"><span class="brand-square"></span><span>Hearthway<br>Studies</span></div>
  <span class="ring" style="left:111px"><span class="sr">Social profile</span></span>
  <span class="ring" style="left:171px"><span class="sr">Social profile</span></span>
  <span class="ring" style="left:231px"><span class="sr">Social profile</span></span>
  <span class="ring" style="left:291px"><span class="sr">Social profile</span></span>

  <div class="col-title" style="left:439px">Quick Links</div>
  <ul class="links" style="left:439px"><li>Home</li><li>About</li><li>Our video</li><li>Contact</li></ul>

  <div class="col-title" style="left:615px">Company</div>
  <ul class="links" style="left:615px"><li>Terms&amp;condtions</li><li>Privacy Policy</li><li>About Us</li><li>Support</li></ul>

  <div class="col-title" style="left:825px">Newsletter Sing Up</div>
  <div class="news-input">Enter Email</div>
  <div class="btn btn-solid">Submit</div>

  <div class="footer-rule"></div>
  <div class="copy">©Copyrights 2022 Hearthway &nbsp;|&nbsp;&nbsp; All Rights Reserved</div>
</footer>

</body>
</html>
```